Australian Trucking Company Requires Professional Looking Stationary

We require a professional looking stationary design that incorporates our newly designed logo.

Our business, called "Brell Haulage Contracting", provides contracting work, transport and logistics to business in Western Australia particularly with links to the mining sector.

We are a small business looking to expand and our new logo and our new stationary will help develop our brand image in our market place.

Target Market(s)

Businesses and Corporation with links to the Mining Sector

Industry/Entity Type

Small Business

Requirements
Must have
• The letterhead must have the following details:
The new logo

Text saying: "Brell Holdings Pty Ltd (ACN 582 316 907) ATF The Brell Discretionary Trust T/AS"
"ABN 71 834 209 553"
Address "P.O Box 817 Wattlegrove WA, 6958"
Phone: 08 9352 7140
Email: brellhaul@mailbox-example.com.au

The text on the letterhead should be editable as the details are likely to change in the near future. Provision should be made for a website address all though one isn't available at the moment.

The styling, layout and font text is entirely up to the designer.

```html
<!DOCTYPE html>
<html lang="en">
<head>
<meta charset="utf-8">
<title>Brell Haulage Contracting – Business Card</title>
<link rel="stylesheet" href="https://fonts.googleapis.com/css2?family=Arimo:wght@400;700&display=swap">
<style>
  :root {
    --backdrop: #ece9e4;
    --card: #ffffff;
    --brand-red: #e3202a;
    --brand-dark-red: #a3141b;
    --text-grey: #555555;
    --icon-grey: #6a6a6a;
    --shadow: rgba(0, 0, 0, 0.18);
  }
  * { box-sizing: border-box; margin: 0; padding: 0; }
  html, body {
    width: 1200px;
    height: 665px;
    overflow: hidden;
    background: var(--backdrop);
    font-family: "Arimo", Arial, sans-serif;
  }
  .stage {
    position: relative;
    width: 1200px;
    height: 665px;
  }
  .card {
    position: absolute;
    width: 540px;
    height: 300px;
    background: var(--card);
    box-shadow: 0 6px 18px var(--shadow);
  }
  .card--front { left: 50px; top: 170px; }
  .card--back { left: 620px; top: 200px; }

  /* Front */
  .person {
    position: absolute;
    top: 34px;
    left: 0;
    width: 100%;
    text-align: center;
    color: var(--brand-red);
    font-size: 17px;
    font-weight: 700;
  }
  .person__divider { margin: 0 8px; }
  .person__title {
    font-size: 12px;
    font-weight: 400;
    color: var(--text-grey);
  }
  .contacts {
    position: absolute;
    top: 82px;
    left: 320px;
    list-style: none;
    color: var(--text-grey);
    font-size: 12px;
  }
  .contacts li {
    display: flex;
    align-items: center;
    gap: 7px;
    height: 19px;
  }
  .contacts svg { width: 11px; height: 11px; flex: none; }
  .brand {
    position: absolute;
    top: 132px;
    left: 34px;
    display: flex;
    align-items: center;
    gap: 10px;
  }
  .brand__mark {
    width: 14px;
    height: 14px;
    background: var(--brand-dark-red);
  }
  .brand__name {
    color: var(--brand-dark-red);
    font-size: 20px;
    font-weight: 700;
    letter-spacing: 0.2px;
  }
  .legal {
    position: absolute;
    left: 0;
    bottom: 34px;
    width: 100%;
    text-align: center;
    color: var(--brand-red);
    font-size: 11.5px;
    line-height: 22px;
  }

  /* Back */
  .back-brand {
    position: absolute;
    top: 110px;
    left: 0;
    width: 100%;
    display: flex;
    justify-content: center;
    align-items: center;
    gap: 12px;
  }
  .back-brand__mark {
    width: 22px;
    height: 22px;
    border-radius: 50%;
    background: var(--brand-red);
  }
  .back-brand__name {
    color: var(--brand-red);
    font-size: 26px;
    font-weight: 700;
  }
  .web {
    position: absolute;
    bottom: 42px;
    width: 100%;
    text-align: center;
    color: var(--brand-red);
    font-size: 12px;
    letter-spacing: 0.5px;
  }
  .web strong { font-size: 14px; }
</style>
</head>
<body>
<main class="stage">
  <section class="card card--front" aria-label="Business card front">
    <p class="person">Name here<span class="person__divider">/</span><span class="person__title">Title</span></p>

    <ul class="contacts">
      <li>
        <svg viewBox="0 0 12 12" aria-hidden="true"><circle cx="6" cy="6" r="5.3" fill="none" stroke="var(--icon-grey)" stroke-width="1"/><path d="M4 3.2c-.6.4-.8 1.2-.4 2.2.5 1.3 1.6 2.4 2.9 2.9 1 .4 1.8.2 2.2-.4L7.6 6.9l-.8.5c-.7-.3-1.3-.9-1.6-1.6l.5-.8z" fill="var(--icon-grey)"/></svg>
        08 9352 7140
      </li>
      <li>
        <svg viewBox="0 0 12 12" aria-hidden="true"><rect x="1" y="2.5" width="10" height="7" fill="var(--icon-grey)"/><path d="M1 2.5l5 4 5-4" fill="none" stroke="#fff" stroke-width="1"/></svg>
        brellhaul@mailbox-example.com.au
      </li>
      <li>
        <svg viewBox="0 0 12 12" aria-hidden="true"><circle cx="6" cy="6" r="5" fill="none" stroke="var(--icon-grey)" stroke-width="1"/><ellipse cx="6" cy="6" rx="2.2" ry="5" fill="none" stroke="var(--icon-grey)" stroke-width="0.8"/><path d="M1 6h10M2 3.5h8M2 8.5h8" stroke="var(--icon-grey)" stroke-width="0.8"/></svg>
        www.brellhaulage-example.com
      </li>
    </ul>

    <div class="brand">
      <span class="brand__mark" aria-hidden="true"></span>
      <span class="brand__name">Brell Haulage Contracting</span>
    </div>

    <p class="legal">
      P.O Box 817 Wattlegrove WA, 6958<br>
      Brell Holdings Pty Ltd (ACN 582 316 907) ATF The Brell Discretionary Trust T/AS
    </p>
  </section>

  <section class="card card--back" aria-label="Business card back">
    <div class="back-brand">
      <span class="back-brand__mark" aria-hidden="true"></span>
      <span class="back-brand__name">Brell Haulage Contracting</span>
    </div>
    <p class="web">www.<strong>brellhaulage-example</strong>.com</p>
  </section>
</main>
</body>
</html>
```